KRT Flyer to attract applicants 11x17

Lantern Stagehand Collective provides crew for local concerts, filming, theater, and corporate events.
The flyer will be posted on bulletin boards at colleges with theater programs.
Our primary venues are historic theaters in downtown LA
Need a 11x17 poster to attract potential applicants/crew
I have attached a poster that one of our staff made that has all if the relevant info - but i know the poster can look much better than that. I have also attached many images and our logo. It is not necessary to use all of the images, or any of them. The two images of the theater interiors are the venues we operate so they would be the first to include. I can send additional info or images upon request. Thank you

Industry/Entity Type

Entertainment

Requirements
Must have
• APPLY@KRTCREW.EXAMPLE

```html
<!DOCTYPE html>
<html lang="en">
<head>
<meta charset="utf-8">
<title>Lantern Stagehand Collective – Open Positions</title>
<link rel="stylesheet" href="https://fonts.googleapis.com/css2?family=Playfair+Display:wght@400;700;800&display=swap">
<style>
  :root {
    --stage-blue: #0a3fb5;
    --deep-blue: #062f94;
    --soft-blue: #1c55c8;
    --accent-cyan: #3fc6e6;
    --paper: #ffffff;
    --backdrop: #eceef2;
    --ink-grey: #6b7280;
  }
  * { margin: 0; padding: 0; box-sizing: border-box; }
  html, body {
    width: 1200px; height: 1200px; overflow: hidden;
    background: var(--backdrop);
  }
  .canvas {
    position: relative; width: 1200px; height: 1200px;
    display: flex; align-items: center; justify-content: center;
  }
  .flyer {
    position: relative; width: 726px; height: 1122px;
    background: var(--stage-blue); overflow: hidden;
    box-shadow: 0 18px 40px rgba(0,0,0,.18);
    font-family: "Playfair Display", Georgia, serif;
    color: var(--paper);
  }
  .flyer__backdrop { position: absolute; inset: 0; }
  .masthead {
    position: absolute; top: 0; left: 0; right: 0; height: 150px;
    background: var(--paper);
    display: flex; align-items: center; padding-left: 48px; gap: 14px;
  }
  .masthead__mark {
    width: 46px; height: 46px; border-radius: 50%;
    background: var(--stage-blue);
  }
  .masthead__name {
    font-size: 25px; font-weight: 700; color: var(--stage-blue);
    line-height: 1.1; max-width: 300px;
  }
  .gallery { position: absolute; top: 150px; left: 0; width: 726px; height: 640px; }
  .headline {
    position: absolute; top: 790px; left: 0; right: 0; text-align: center;
    font-size: 58px; font-weight: 800; letter-spacing: 2px;
  }
  .intro {
    position: absolute; top: 870px; left: 90px; right: 90px; text-align: center;
    font-size: 19px; line-height: 1.45;
  }
  .ribbon {
    position: absolute; top: 950px; left: 50%; transform: translateX(-50%);
    width: 600px; height: 58px;
  }
  .ribbon svg { position: absolute; inset: 0; }
  .ribbon__text {
    position: relative; z-index: 1; height: 58px;
    display: flex; align-items: center; justify-content: center;
    color: var(--stage-blue); font-size: 22px; font-weight: 700; letter-spacing: .5px;
  }
  .web-address {
    position: absolute; top: 1030px; left: 0; right: 0; text-align: center;
    font-size: 20px; font-weight: 700; letter-spacing: 1px;
  }
  .foot-band {
    position: absolute; bottom: 0; left: 0; right: 0; height: 34px;
    background: var(--deep-blue); border-top: 6px solid var(--paper);
  }
</style>
</head>
<body>
<main class="canvas">
  <article class="flyer">
    <svg class="flyer__backdrop" width="726" height="1122" viewBox="0 0 726 1122" aria-hidden="true">
      <path d="M0 420 C120 380 200 520 140 640 C90 740 0 720 0 720 Z" fill="var(--soft-blue)"/>
      <path d="M726 560 C620 600 600 760 700 820 L726 830 Z" fill="var(--soft-blue)"/>
      <path d="M0 960 C140 930 260 1020 240 1122 L0 1122 Z" fill="var(--soft-blue)"/>
    </svg>

    <header class="masthead">
      <span class="masthead__mark" aria-hidden="true"></span>
      <span class="masthead__name">Lantern Stagehand Collective</span>
    </header>

    <svg class="gallery" width="726" height="640" viewBox="0 0 726 640">
      <defs>
        <linearGradient id="theater-tones" x1="0" y1="0" x2="1" y2="1">
          <stop offset="0" stop-color="#d98a2c"/>
          <stop offset=".55" stop-color="#a4521c"/>
          <stop offset="1" stop-color="#5a2a12"/>
        </linearGradient>
        <linearGradient id="skyline-tones" x1="0" y1="0" x2="0" y2="1">
          <stop offset="0" stop-color="#1b2a55"/>
          <stop offset=".6" stop-color="#2f6fa8"/>
          <stop offset="1" stop-color="#0b1430"/>
        </linearGradient>
        <linearGradient id="crowd-tones" x1="0" y1="0" x2="0" y2="1">
          <stop offset="0" stop-color="#9aa6c6"/>
          <stop offset=".55" stop-color="#4c5677"/>
          <stop offset="1" stop-color="#111522"/>
        </linearGradient>
      </defs>
      <circle cx="370" cy="110" r="48" fill="var(--accent-cyan)" opacity=".35"/>
      <circle cx="140" cy="210" r="44" fill="var(--accent-cyan)" opacity=".35"/>
      <circle cx="560" cy="380" r="44" fill="var(--accent-cyan)" opacity=".35"/>
      <circle cx="140" cy="470" r="40" fill="var(--paper)" opacity=".15"/>
      <path role="img" aria-label="Photo of an ornate historic theater interior with gilded balconies"
            d="M400 40 C470 -10 620 0 665 70 C710 150 660 270 570 310 C480 350 380 300 370 210 C360 130 360 70 400 40 Z"
            fill="url(#theater-tones)"/>
      <path role="img" aria-label="Photo of a downtown city skyline at night"
            d="M70 280 C120 230 260 235 310 280 C350 320 330 400 260 420 C180 440 80 410 60 360 C50 330 55 300 70 280 Z"
            fill="url(#skyline-tones)"/>
      <path role="img" aria-label="Photo of a concert crowd with raised hands in silhouette"
            d="M260 450 C320 410 430 430 450 500 C470 570 430 620 350 620 C270 620 220 580 225 520 C228 490 240 465 260 450 Z"
            fill="url(#crowd-tones)"/>
    </svg>

    <h1 class="headline">HAS OPEN POSITIONS</h1>
    <p class="intro">We are looking for talented technicians to add to our roster of skilled professionals.</p>

    <div class="ribbon">
      <svg width="600" height="58" viewBox="0 0 600 58" aria-hidden="true">
        <polygon points="0,0 600,0 578,29 600,58 0,58 22,29" fill="var(--paper)"/>
      </svg>
      <p class="ribbon__text">Send Resume to : APPLY@KRTCREW.EXAMPLE</p>
    </div>

    <p class="web-address">www.krtcrew.example</p>
    <div class="foot-band" aria-hidden="true"></div>
  </article>
</main>
</body>
</html>
```